Larkspur Talent IT Recruiting firm needs a business card design for Recruiters, Sourcers, and Account

We need business cards that allow us to change all contact info, names, titles (Recruiter, Sourcer, Account Manager, Director, CEO, etc) per person since we have three offices, in three cities, Phoenix, Austin, and Las Vegas. We do recruiting and contractors for IT positions (Developers, Architects, Software Engineers, Security Engineers, Help Desk, DBAs, PMs, Scrum Masters, etc.) Our client companies are very diverse from Meridian 100 to silicone Valley type start-ups.

So, while we what hip, techie, and quirky, it still needs to be professional. Primary color we use is blue, with silver as a secondary color.

Target Market(s)

IT, Technology

Industry/Entity Type

Business

Contact Information for Business Card

Company name: Larkspur Talent, Inc.
Website: www.larkspurtalent.example
Logos for Careerloop, Blipster, and Myriada

Name, Title, Office Number, Cell Number, email

Font styles to use
Serif
Sans Serif

Colors
0455a3
d5d5d5

Requirements
Nice to have
• The grey I selected below is not necessary - but, would like silver included. I included a card design (File 3: LTI early trial example.jpg) that I had started on. It's very rough, and not quite what we're looking for, but what we did like is the logo, big, maybe a bit faded, off center, goes out of frame, etc. Still looking for other ideas - you are the pros! But, just an idea of a design element we liked.

```html
<!DOCTYPE html>
<html lang="en">
<head>
<meta charset="utf-8">
<title>Larkspur Talent — Business Card</title>
<link rel="stylesheet" href="https://fonts.googleapis.com/css2?family=Cinzel:wght@400&family=Open+Sans:wght@400;700&display=swap">
<style>
  :root {
    --brand-blue: #0455a3;
    --silver: #d5d5d5;
    --ink: #1c1c1c;
    --card-white: #ffffff;
    --stage: #ecebe8;
    --card-edge: #3a3a3a;
    --rule: #9a9a9a;
  }
  * { box-sizing: border-box; margin: 0; padding: 0; }
  html, body {
    width: 1200px; height: 1094px; overflow: hidden;
    background: var(--stage);
  }
  .card {
    position: absolute;
    width: 842px; height: 481px;
    background: var(--card-white);
    border: 1.5px solid var(--card-edge);
    border-radius: 30px;
    overflow: hidden;
  }
  .card--details { left: 306px; top: 41px; }
  .card--cover { left: 52px; top: 569px; }

  /* Wordmark */
  .wordmark {
    position: absolute;
    display: flex; align-items: center; gap: 16px;
  }
  .wordmark__dot {
    width: 70px; height: 70px; border-radius: 50%;
    background: var(--brand-blue);
    flex: none;
  }
  .wordmark__name {
    font-family: 'Cinzel', serif;
    font-weight: 400;
    color: var(--ink);
    font-size: 50px;
    line-height: 0.95;
    letter-spacing: 2px;
  }
  .wordmark__name span { display: block; white-space: nowrap; }
  .wordmark__name span + span { text-align: right; }

  .tagline {
    position: absolute;
    font-family: 'Cinzel', serif;
    font-size: 21px;
    letter-spacing: 2.6px;
    color: var(--ink);
    white-space: nowrap;
    transform: translate(-50%, -50%);
  }

  /* Details side */
  .card--details .wordmark { left: 50px; top: 125px; }
  .card--details .tagline { left: 241px; top: 259px; }
  .divider {
    position: absolute; left: 476px; top: 104px;
    width: 1.5px; height: 170px; background: var(--rule);
  }
  .contact-list {
    position: absolute; left: 510px; top: 112px;
    list-style: none;
    font-family: 'Open Sans', sans-serif;
    font-size: 19.5px; color: var(--ink);
  }
  .contact-list li {
    display: flex; align-items: center; gap: 8px;
    height: 32.5px; white-space: nowrap;
  }
  .contact-list svg { width: 17px; height: 17px; flex: none; }
  .swoosh { position: absolute; left: 0; top: 0; width: 842px; height: 481px; }
  .name-bar {
    position: absolute; left: 0; right: 0; bottom: 12px;
    text-align: center;
    font-family: 'Open Sans', sans-serif;
    color: #fff;
    font-size: 19px;
  }
  .name-bar__name { font-weight: 700; font-size: 24px; }

  /* Cover side */
  .card--cover .wordmark { left: 50%; top: 98px; transform: translateX(-50%); }
  .card--cover .wordmark__name { font-size: 64px; }
  .card--cover .wordmark__dot { width: 84px; height: 84px; }
  .card--cover .tagline { left: 421px; top: 270px; font-size: 24px; letter-spacing: 3px; }
  .site-url {
    position: absolute; left: 0; right: 0; top: 364px;
    text-align: center;
    font-family: 'Open Sans', sans-serif;
    font-size: 25px; letter-spacing: 3px;
    color: var(--ink);
  }
</style>
</head>
<body>

  <section class="card card--details">
    <svg class="swoosh" viewBox="0 0 842 481" aria-hidden="true">
      <path d="M0,308 C180,395 470,428 760,418 C610,432 250,418 0,346 Z" fill="var(--silver)"/>
      <path d="M0,346 C220,410 470,432 842,394 L842,481 L0,481 Z" fill="var(--brand-blue)"/>
    </svg>

    <div class="wordmark">
      <div class="wordmark__dot"></div>
      <div class="wordmark__name"><span>LARKSPUR</span><span>TALENT</span></div>
    </div>
    <p class="tagline">CONNECTING TECH TALENT</p>

    <div class="divider"></div>

    <ul class="contact-list">
      <li>
        <svg viewBox="0 0 16 16" aria-hidden="true"><path d="M4 1.5 L6.5 4.5 L5 6.2 C5.8 8 7.8 10 9.8 11 L11.5 9.5 L14.5 12 L12.8 14.3 C7.5 14 2 8.5 1.7 3.2 Z" fill="none" stroke="var(--brand-blue)" stroke-width="1.5" stroke-linejoin="round"/></svg>
        555-014-2736
      </li>
      <li>
        <svg viewBox="0 0 16 16" aria-hidden="true"><rect x="1" y="3.5" width="14" height="10" rx="1.5" fill="var(--brand-blue)"/><path d="M1.5 4.5 L8 9.5 L14.5 4.5" fill="none" stroke="#fff" stroke-width="1.3"/></svg>
        maya@larkspurtalent.example
      </li>
      <li>
        <svg viewBox="0 0 16 16" aria-hidden="true"><g fill="none" stroke="var(--brand-blue)" stroke-width="1.3"><circle cx="8" cy="8" r="6.5"/><ellipse cx="8" cy="8" rx="2.8" ry="6.5"/><path d="M1.5 8 H14.5 M2.6 4.6 H13.4 M2.6 11.4 H13.4"/></g></svg>
        www.larkspurtalent.example
      </li>
      <li>
        <svg viewBox="0 0 16 16" aria-hidden="true"><circle cx="8" cy="8" r="7" fill="var(--brand-blue)"/></svg>
        @MayaRowanLT
      </li>
      <li>
        <svg viewBox="0 0 16 16" aria-hidden="true"><circle cx="8" cy="8" r="7" fill="var(--brand-blue)"/></svg>
        @MayaRowanLT
      </li>
    </ul>

    <p class="name-bar"><span class="name-bar__name">Maya Rowan,</span> First Touch Embassador</p>
  </section>

  <section class="card card--cover">
    <div class="wordmark">
      <div class="wordmark__dot"></div>
      <div class="wordmark__name"><span>LARKSPUR</span><span>TALENT</span></div>
    </div>
    <p class="tagline">CONNECTING TECH TALENT</p>
    <p class="site-url">www.larkspurtalent.example</p>
  </section>

</body>
</html>
```